Vantro cards

I am in the auto motive, transportation business I would like a business card that is Something cool, modern edgy, having to do with car culture. I offer towing service for high and exotic cars. I also provide towing for collisions and car accidents. I offer open and enclosed transport nationwide.

Target Market(s)

Car culture people high end auto collectors

Industry/Entity Type

Towing car carrier

Contact Information for Business Card

My company colors black yellow and silver

Font styles to use
Serif

```html
<!DOCTYPE html>
<html lang="en">
<head>
<meta charset="utf-8">
<title>Vantro Business Card</title>
<link href="https://fonts.googleapis.com/css2?family=Arimo:wght@400;700&display=swap" rel="stylesheet">
<style>
  :root {
    --bg: #e9e9e9;
    --card: #333333;
    --card-edge: #f0cf3c;
    --yellow: #f2cb3a;
    --white: #f4f4f4;
    --muted: #d9d9d9;
    --divider: #8a8a8a;
    --emboss: #2a2a2a;
  }
  html, body {
    margin: 0;
    padding: 0;
    width: 1200px;
    height: 802px;
    overflow: hidden;
    background: var(--bg);
    font-family: "Arimo", Arial, sans-serif;
  }
  .stage {
    position: relative;
    width: 1200px;
    height: 802px;
  }
  .card {
    position: absolute;
    top: 246px;
    width: 540px;
    height: 309px;
    background: var(--card);
    border: 2px solid var(--card-edge);
    box-sizing: border-box;
    box-shadow: 0 6px 18px rgba(0,0,0,0.18);
  }
  .card-front { left: 45px; }
  .card-back { left: 615px; }

  .front-brand {
    position: absolute;
    left: 40px;
    top: 0;
    width: 200px;
    height: 100%;
    display: flex;
    align-items: center;
    justify-content: center;
  }
  .brand-name {
    font-weight: 700;
    font-size: 40px;
    letter-spacing: 2px;
    color: var(--white);
    text-transform: uppercase;
  }
  .divider {
    position: absolute;
    left: 262px;
    top: 72px;
    width: 1px;
    height: 165px;
    background: var(--divider);
  }
  .contact {
    position: absolute;
    left: 286px;
    top: 70px;
    color: var(--white);
  }
  .person-name {
    margin: 0;
    font-size: 19px;
    font-weight: 700;
    color: var(--yellow);
    letter-spacing: 0.5px;
  }
  .person-role {
    margin: 3px 0 14px;
    font-size: 14px;
    color: var(--muted);
  }
  .address {
    margin: 0 0 12px;
    font-size: 14px;
    line-height: 1.35;
    color: var(--muted);
  }
  .contact-list {
    list-style: none;
    margin: 0;
    padding: 0;
    font-size: 14px;
    color: var(--muted);
  }
  .contact-list li {
    display: flex;
    align-items: center;
    gap: 9px;
    line-height: 21px;
  }
  .contact-icon {
    width: 12px;
    height: 12px;
    flex: none;
  }
  .back-brand {
    position: absolute;
    inset: 0;
    display: flex;
    align-items: center;
    justify-content: center;
  }
  .back-brand .brand-name {
    font-size: 64px;
    color: var(--emboss);
    letter-spacing: 4px;
  }
</style>
</head>
<body>
<main class="stage">
  <section class="card card-front" aria-label="Card front">
    <div class="front-brand">
      <span class="brand-name">Vantro</span>
    </div>
    <div class="divider"></div>
    <div class="contact">
      <h1 class="person-name">MARCUS HALE</h1>
      <p class="person-role">Manager</p>
      <p class="address">Your Address, City<br>State, Zip 0000</p>
      <ul class="contact-list">
        <li>
          <svg class="contact-icon" viewBox="0 0 12 12" aria-hidden="true">
            <circle cx="6" cy="6" r="6" fill="var(--yellow)"/>
            <path d="M3.6 3.2c.4-.4.8-.3 1 0l.6.9c.2.3.1.6-.1.8l-.3.3c.3.7.8 1.2 1.5 1.5l.3-.3c.2-.2.5-.3.8-.1l.9.6c.3.2.4.6 0 1-.8.8-2 .6-3.2-.5S2.8 4 3.6 3.2z" fill="var(--card)"/>
          </svg>
          <span>123-456-2100</span>
        </li>
        <li>
          <svg class="contact-icon" viewBox="0 0 12 12" aria-hidden="true">
            <rect x="0.5" y="2.5" width="11" height="7.5" fill="var(--yellow)"/>
            <path d="M0.5 2.5L6 7l5.5-4.5" fill="none" stroke="var(--card)" stroke-width="1"/>
          </svg>
          <span>youremail@mailbox.com</span>
        </li>
        <li>
          <svg class="contact-icon" viewBox="0 0 12 12" aria-hidden="true">
            <circle cx="6" cy="6" r="6" fill="var(--yellow)"/>
            <ellipse cx="6" cy="6" rx="2.3" ry="5" fill="none" stroke="var(--card)" stroke-width="0.9"/>
            <path d="M1 6h10" stroke="var(--card)" stroke-width="0.9"/>
          </svg>
          <span>www.yourwebsite.com</span>
        </li>
      </ul>
    </div>
  </section>

  <section class="card card-back" aria-label="Card back">
    <div class="back-brand">
      <span class="brand-name">Vantro</span>
    </div>
  </section>
</main>
</body>
</html>
```